Automotive eCommerce Business looking for a business card design

Looking for a clean and simple business card design. Our company name is "Brindle Auto" and we are a company specializing in the ecommerce sales of automotive parts, specifically for pick up trucks and large SUVs. Our company colours are red, black, and white.

Feel free to use the logo provided or create a new logo that you seem fit. Looking forward to your creative ideas!

Industry/Entity Type

Automotive

Contact Information for Business Card

We were thinking of a possibly two-sided design featuring just the logo and company name on one side, and personal information on the other side. Single sided designs will be considered as well.

Font styles to use
Serif
Sans Serif
Decorative

Colors
ec1f27
ffffff
000000

Requirements
Must have
• Space for employee's name, title, phone number and email address, along with the company address and website somewhere.

```html
<!DOCTYPE html>
<html lang="en">
<head>
<meta charset="utf-8">
<title>Brindle Auto – Business Card</title>
<link rel="stylesheet" href="https://fonts.googleapis.com/css2?family=Cinzel:wght@400;500&family=Roboto:wght@400&display=swap">
<style>
  :root {
    --backdrop: #2b2b2b;
    --paper: #f2f2f2;
    --brand-red: #9e1c20;
    --ink: #4a4a4a;
    --ink-soft: #5c5c5c;
    --rule: #8a8a8a;
    --band-grey: #4b4b4b;
    --white: #ffffff;
  }
  * { margin: 0; padding: 0; box-sizing: border-box; }
  html, body {
    width: 1200px; height: 960px; overflow: hidden;
    background: var(--backdrop);
  }
  .canvas { position: relative; width: 1200px; height: 960px; }

  .card {
    position: absolute; width: 600px; height: 342px; overflow: hidden;
  }
  .card-front { left: 314px; top: 113px; background: var(--paper); }
  .card-back { left: 311px; top: 472px; background: var(--brand-red); }

  .name-tab {
    position: absolute; left: 0; top: 135px; width: 14px; height: 40px;
    background: var(--brand-red);
  }
  .person { position: absolute; left: 35px; top: 133px; }
  .person-name {
    font-family: "Cinzel", serif; font-weight: 500;
    font-size: 21px; color: var(--brand-red); line-height: 26px;
  }
  .person-title {
    font-family: "Cinzel", serif; font-size: 16px;
    color: var(--ink-soft); line-height: 22px; letter-spacing: 0.5px;
  }

  .brand-mark {
    position: absolute; left: 446px; top: 40px; width: 60px; height: 60px;
    background: var(--brand-red);
  }
  .brand-name {
    position: absolute; right: 35px; top: 152px;
    font-family: "Cinzel", serif; font-weight: 500;
    font-size: 19px; color: var(--ink); letter-spacing: 0.5px;
  }

  .divider {
    position: absolute; left: 35px; top: 193px; width: 528px; height: 1px;
    background: var(--rule);
  }

  .contact-list {
    position: absolute; left: 35px; top: 216px; list-style: none;
    font-family: "Roboto", sans-serif; font-size: 14px; color: var(--ink);
  }
  .contact-list li { display: flex; align-items: center; height: 19px; }
  .contact-list svg { width: 14px; height: 14px; margin-right: 9px; fill: var(--brand-red); }

  .address {
    position: absolute; right: 36px; top: 254px; text-align: right;
    font-family: "Roboto", sans-serif; font-size: 14px; line-height: 19px;
    color: var(--ink);
  }

  .front-bands { position: absolute; left: 0; top: 0; }
  .front-url {
    position: absolute; right: 16px; top: 315px;
    font-family: "Roboto", sans-serif; font-size: 14px;
    letter-spacing: 3px; color: var(--white);
  }

  .back-brand {
    position: absolute; right: 30px; top: 262px; text-align: right;
    color: var(--white);
  }
  .back-brand-name {
    font-family: "Cinzel", serif; font-weight: 500; font-size: 22px; line-height: 28px;
  }
  .back-url {
    font-family: "Roboto", sans-serif; font-size: 13px; letter-spacing: 3px;
  }
</style>
</head>
<body>
<main class="canvas">

  <section class="card card-front">
    <div class="name-tab"></div>
    <div class="person">
      <p class="person-name">Marcus Hale</p>
      <p class="person-title">CEO/Founder</p>
    </div>

    <div class="brand-mark"></div>
    <p class="brand-name">Brindle Auto Ltd.</p>

    <div class="divider"></div>

    <ul class="contact-list">
      <li>
        <svg viewBox="0 0 16 16" aria-hidden="true"><path d="M3.5 1l3 3-1.6 2.1c.9 1.9 2.3 3.3 4.2 4.2L11.2 8.7l3 3-1.5 2.6C7 14 2 9 1.7 3.3z"/></svg>
        555 214 3307
      </li>
      <li>
        <svg viewBox="0 0 16 16" aria-hidden="true"><path d="M4.5 0h7v16h-7zM5.8 1.6v10.8h4.4V1.6zM7.3 13.3h1.4v1.4H7.3z"/></svg>
        555 781 4620
      </li>
      <li>
        <svg viewBox="0 0 16 16" aria-hidden="true"><path d="M4 1h8v4H4zM1 6h14v6h-2V9H3v3H1zM4 10h8v5H4z"/></svg>
        555 390 1172
      </li>
      <li>
        <svg viewBox="0 0 16 16" aria-hidden="true"><path d="M1 4h14v9H1zM2.4 5.2L8 9.2l5.6-4z" fill-rule="evenodd"/></svg>
        marcus@brindleauto.com
      </li>
    </ul>

    <p class="address">2140 Larkspur Road<br>Fairbanks, Alaska 99701</p>

    <svg class="front-bands" width="600" height="342" viewBox="0 0 600 342" aria-hidden="true">
      <path d="M0 322 L322 322 Q332 322 338 316 L338 331 L0 331 Z" fill="#4b4b4b"/>
      <path d="M0 332 L326 332 Q340 332 346 320 L352 312 Q357 308 366 308 L600 308 L600 342 L0 342 Z" fill="#9e1c20"/>
      <path d="M0 331.5 L326 331.5 Q339 331.5 345 320" fill="none" stroke="#ffffff" stroke-width="1.2"/>
    </svg>
    <p class="front-url">www.brindleauto.com</p>
  </section>

  <section class="card card-back">
    <div class="back-brand">
      <p class="back-brand-name">BRINDLE AUTO LTD</p>
      <p class="back-url">www.brindleauto.com</p>
    </div>
  </section>

</main>
</body>
</html>
```